KVR Inc Web Design

WHAT ARE WE DOING?
We are developing a new website look and feel for a new company called KVR Inc. This new look and feel should include colors, design elements, choice of photography and other imagery, fonts, and other user experience elements.

WHAT DO THEY DO?
KVR, Inc, makes tools for researchers who are studying protein-protein interactions. These molecules are the basic tools of biology, and serve as key targets for drug developers and disease researchers. The world of proteins is enormously complex, and companies like KVR provide researchers with critical tools that help them elucidate this world.

WHO ARE WE TALKING TO?
The target audience for this website are professional scientists working in university research or biopharma drug development. They are highly sophisticated consumers looking for key tools that will advance their research.

WHAT DO WE WANT THEM TO DO?
The site is an information resource for the customer exploring the tools that KVR sells and the scientific issues surrounding protein-protein interactions. They should be able to navigate easily to their content of choice, while the whole site should convey a professionalism that enhanced KVR’s credibility.

WHAT DOES THE KVR BRAND STAND FOR?
KVR stands for illumination. Proteins are challenging to study, and KVR exists to help shed light on their workings.

WHAT ARE THE KEY VALUES OF THE KVR BRAND?
Integrity. Innovation. Insight.

WHAT ARE THE EXECUTIONAL MANDITORIES?
The look and feel is completely up for grabs. Nothing is off the table.

WHAT ARE THE DELIVERABLES?
We need new designs for the following templates:
http://cms.marlowbench.com/
http://cms.marlowbench.com/products-and-services/instruments-3/bench-top-instruments/
http://cms.marlowbench.com/category/lab-study/

```html
<!DOCTYPE html>
<html lang="en">
<head>
<meta charset="utf-8">
<title>KVR Inc – Pipettes</title>
<link href="https://fonts.googleapis.com/css2?family=Figtree:wght@400;500;600;700&family=Open+Sans:wght@400&display=swap" rel="stylesheet">
<style>
:root{
  --header:#fdb94c;
  --header-text:#fff;
  --pill:#6b4b2c;
  --ink:#111;
  --body:#555;
  --rule:#cfcfcf;
  --accent:#31b3d6;
  --tab-line:#fafafa;
  --search:#d89a3d;
  --dropdown:#b9b9b9;
  --footer-text:#555;
  --social:#5a5a5a;
}
*{box-sizing:border-box;margin:0;padding:0}
html,body{width:1200px;height:1110px;overflow:hidden;background:#fff}
body{font-family:"Figtree",sans-serif;color:var(--ink);position:relative}
.site-header{position:absolute;left:0;top:0;width:1200px;height:62px;background:var(--header)}
.brand{position:absolute;left:190px;top:15px;font-size:24px;font-weight:400;letter-spacing:4px;color:var(--header-text);line-height:30px;white-space:nowrap}
.main-nav{position:absolute;left:340px;top:16px;display:flex;gap:2px}
.main-nav a{display:block;padding:0 8px;height:26px;line-height:26px;border-radius:13px;color:var(--header-text);font-weight:600;font-size:13.5px;text-decoration:none;white-space:nowrap}
.main-nav a.is-active{background:var(--pill)}
.search{position:absolute;left:892px;top:18px;width:118px;height:21px;background:var(--search);color:#fbe3bd;font-size:11px;line-height:21px;padding-left:6px}
.search svg{position:absolute;right:5px;top:5px}
.page-title{position:absolute;left:190px;top:103px;font-size:23px;font-weight:500;letter-spacing:.5px}
.product-select{position:absolute;left:844px;top:106px;width:166px;height:22px;background:var(--dropdown);color:#fff;font-size:11px;line-height:22px;padding-left:13px}
.product-select svg{position:absolute;right:8px;top:9px}
.title-rule{position:absolute;left:190px;top:135px;width:820px;height:3px;border-top:1px solid var(--rule);border-bottom:1px solid var(--rule)}
.lead{position:absolute;left:190px;top:148px;width:790px;font-size:18px;line-height:23px;font-weight:400}
.hero{position:absolute;left:190px;top:212px;width:820px;height:288px;background:linear-gradient(90deg,#c9a98a 0%,#7f8fa6 30%,#3b7fc8 55%,#3a88d2 80%,#4c9ae0 100%)}
.copy{position:absolute;left:190px;top:524px;width:820px;font-size:11px;line-height:16px;color:var(--body)}
.copy p+p{margin-top:16px}
.tabs{position:absolute;left:190px;top:724px;width:217px;list-style:none}
.tabs li{height:40.6px;line-height:40px;padding-left:24px;font-size:15px;background:linear-gradient(90deg,#e6e6e6,#f3f3f3);border-bottom:1px solid var(--tab-line);position:relative}
.tabs li.is-active{background:var(--accent);color:#fff}
.tabs li.is-active svg{position:absolute;right:-13px;top:0}
.feature-photo{position:absolute;left:442px;top:724px;width:264px;height:206px;background:linear-gradient(135deg,#e9eef2 0%,#cdd8e0 45%,#8fb0cc 100%)}
.feature-text{position:absolute;left:716px;top:723px;width:290px;font-size:11px;line-height:16px;color:var(--body)}
.feature-text strong{font-weight:700;color:#444}
.feature-text p+p{margin-top:16px}
.footer-rule{position:absolute;left:190px;top:981px;width:820px;height:3px;border-top:1px solid var(--rule);border-bottom:1px solid #e4e4e4}
.footer-mark{position:absolute;left:589px;top:1005px;width:23px;height:3px;background:var(--header)}
.footer-mark::after{content:"";position:absolute;left:9px;top:0;width:4px;height:3px;background:var(--pill)}
.footer-nav{position:absolute;left:0;top:1019px;width:1200px;text-align:center;font-family:"Open Sans",sans-serif;font-size:10.5px;color:var(--footer-text)}
.footer-nav span{margin:0 5px}
.copyright{position:absolute;left:0;top:1037px;width:1200px;text-align:center;font-family:"Open Sans",sans-serif;font-size:11px;color:var(--footer-text)}
.social{position:absolute;left:571px;top:1056px;display:flex;gap:3px}
.social span{display:block;width:17px;height:17px;border-radius:50%;background:var(--social)}
</style>
</head>
<body>
<header class="site-header">
  <div class="brand">KVR INC</div>
  <nav class="main-nav">
    <a href="#">Company</a>
    <a href="#" class="is-active">Products &amp; Services</a>
    <a href="#">Learning Center</a>
    <a href="#">Events</a>
    <a href="#">KVR News</a>
    <a href="#">Contact</a>
  </nav>
  <div class="search">Search
    <svg width="11" height="11" viewBox="0 0 11 11"><circle cx="4.5" cy="4.5" r="3.5" fill="none" stroke="#fbe3bd" stroke-width="1.3"/><line x1="7" y1="7" x2="10" y2="10" stroke="#fbe3bd" stroke-width="1.5"/></svg>
  </div>
</header>

<h1 class="page-title">PIPETTES</h1>
<div class="product-select">Product Overview
  <svg width="11" height="6" viewBox="0 0 11 6"><path d="M0 0h11L5.5 6z" fill="#fff"/></svg>
</div>
<div class="title-rule"></div>

<p class="lead">Donec non massa lacinia, commodo eros eget, rutrum arcu. Integer tincidunt, velit id eleifend congue, odio massa consequat mauris, massa consequat</p>

<div class="hero" role="img" aria-label="Scientist in protective gear using a pipette against a blue background"></div>

<div class="copy">
  <p>Quisque feugiat lacus vitae posuere blandit. Nulla sit amet laoreet felis, id rhoncus nisl. Aenean fringilla quam in nibh egestas, in malesuada tortor accumsan. Donec non massa lacinia, commodo eros eget, rutrum arcu. Integer tincidunt, velit id eleifend congue, odio massa consequat mauris, a scelerisque nulla nulla eu nulla. Cras luctus pulvinar nibh ut viverra. Aenean vestibulum vitae justo non dictum. Mauris ut tellus in dui pretium dictum nec non tortor. Nulla a velit quis dolor interdum scelerisque eu et nisl.</p>
  <p>Donec auctor mollis ligula eget molestie. Aliquam erat volutpat. Curabitur sapien libero, condimentum ac nisl nec, ultricies tincidunt ipsum. Donec in iaculis metus. Mauris eleifend nisi non sapien commodo, hendrerit ornare lacus consectetur. Pellentesque faucibus, purus non dictum lacinia, ante augue pretium neque, vitae egestas dui nisl et enim. Suspendisse iaculis nibh vel lacinia rhoncus Donec auctor mollis ligula eget molestie. Aliquam erat volutpat. Curabitur sapien libero, condimentum ac nisl nec, ultricies tincidunt ipsum. Donec in iaculis metus. Mauris eleifend nisi non sapien commodo, hendrerit ornare lacus consectetur. Pellentesque faucibus, purus non dictum lacinia, ante augue pretium neque, vitae egestas dui nisl et enim.</p>
</div>

<ul class="tabs">
  <li>Overview</li>
  <li class="is-active">Features
    <svg width="13" height="40" viewBox="0 0 13 40"><path d="M0 0L13 20L0 40z" fill="#31b3d6"/></svg>
  </li>
  <li>Specifications</li>
  <li>FAQ's</li>
  <li>Manuals</li>
</ul>

<div class="feature-photo" role="img" aria-label="Two researchers in lab coats examining a seedling in a test tube"></div>

<div class="feature-text">
  <p><strong>Quisque feugiat lacus vitae posuere blandit. Nulla sit amet laoreet felis, id rhoncus nisl. Aenean fringilla</strong> quam in nibh egestas, in malesuada tortor accumsan. Donec non massa lacinia, commodo eros eget, rutrum arcu. Integer tincidunt, velit id eleifend congue, odio massa consequat mauris, a scelerisque nulla nulla eu nulla. Cras luctus pulvinar nibh ut viverra. Aenean vestibulum vitae justo non dictum. Mauris ut tellus in dui pretium dictum nec non tortor.</p>
  <p>Nulla a velit quis dolor interdum scelerisque eu et nisl. Donec auctor mollis ligula eget molestie. Aliquam erat volutpat. Curabitur sapien libero</p>
</div>

<footer>
  <div class="footer-rule"></div>
  <div class="footer-mark"></div>
  <nav class="footer-nav">Company<span>-</span>Products &amp; Services<span>-</span>Learning Center<span>-</span>Events<span>-</span>KVR News<span>-</span>Contact</nav>
  <p class="copyright">Copyright © KVR Inc. 2013</p>
  <div class="social" aria-label="Social links"><span></span><span></span><span></span></div>
</footer>
</body>
</html>
```